Website Development for vaultmerrow.com.au

Build a new Wordpress/Responsive website for vaultmerrow.com.au

Target Market(s)

Compliance Managers, Risk Managers, Information Security and Cyber Security Professionals, Chief Data/Digital Officers, Chief Operating/Financial Officers, Business Continuity Professionals, Disaster Recovery Planners, Small Business Owners, Local/Federal Government entities

Industry/Entity Type

Data Service

Coding

Coded - Design and coding required

Number of Pages Required

5+ page

Font styles to use
Sans Serif

Colors

Designer to choose colors to be used in the design.

Requirements
Must have
• 1. Site Structure: Home Page plus the following chapter-pages for a) Services b) About c) Resources d) Blog e) Contact Us
• 2. Prefer site to built on wordpress and we can purchase a theme if needed (we currently use Kelp9 for other sites)
• 3. Blog needs to be wordpress based
• 4. We will host the site ourselves on our own servers
• 5. Responsive Design
Nice to have
• 1. Livechat capability/interface
• 2. Capability for marketing automation integration (such as hubspot, marketo, infusionsoft etc)
• 3. Capability for CRM integration (Salesforce)

```html
<!DOCTYPE html>
<html lang="en">
<head>
<meta charset="utf-8">
<title>Vault Merrow — Home</title>
<link rel="stylesheet" href="https://fonts.googleapis.com/css2?family=Mulish:wght@400;600;700;800&family=Roboto:wght@400;500;700&display=swap">
<style>
:root{
  --blue:#1d64b4;
  --blue-dark:#0f4a8f;
  --blue-deep:#0b2f5c;
  --sky:#e6f0fb;
  --ink:#2b2b2b;
  --muted:#6b6b6b;
  --line:#d9d9d9;
  --white:#ffffff;
  --footer:#1e1f22;
  --social-red:#e0533d;
}
*{box-sizing:border-box;margin:0;padding:0}
html,body{width:1200px;height:4433px;overflow:hidden}
body{position:relative;background:var(--white);font-family:'Mulish',sans-serif;color:var(--ink)}
.abs{position:absolute}
.brand{font-family:'Mulish',sans-serif;font-weight:800;color:var(--blue);display:flex;align-items:center;gap:10px}
.brand .mark{width:30px;height:30px;background:var(--blue);border-radius:50%}
.heading{font-family:'Roboto',sans-serif;font-weight:500;text-align:center;color:var(--ink);letter-spacing:1px}

/* top bar */
.topbar{top:0;left:0;width:1200px;height:36px;font-size:14px;color:var(--muted)}
.topbar .contact{left:140px;top:10px;display:flex;gap:36px}
.topbar .contact span{display:flex;align-items:center;gap:8px}
.topbar .follow{left:858px;top:8px;display:flex;align-items:center;gap:6px;font-size:14px;color:var(--ink)}
.sq{width:20px;height:20px;border-radius:3px;display:inline-block}
.header{top:36px;left:0;width:1200px;height:72px}
.header .brand{position:absolute;left:140px;top:12px;font-size:30px}
.nav{position:absolute;left:520px;top:36px;display:flex;gap:0;font-size:13px;font-weight:700;color:var(--ink)}
.nav a{text-decoration:none;color:inherit;padding:0 24px 12px}
.nav a.active{color:var(--blue);border-bottom:3px solid var(--blue)}

/* hero */
.hero{top:108px;left:0;width:1200px;height:610px;background:linear-gradient(100deg,#0c2a4f 0%,#1a4f86 45%,#3d6fa2 70%,#172a44 100%);overflow:hidden}
.hero h1{position:absolute;left:140px;top:212px;font-family:'Roboto',sans-serif;font-weight:700;font-size:38px;line-height:46px;color:var(--white)}
.btn-light{position:absolute;left:140px;top:326px;width:186px;height:46px;background:var(--white);color:var(--blue-dark);font-weight:700;font-size:15px;display:flex;align-items:center;justify-content:center}
.hero svg.curve{position:absolute;left:0;bottom:0}

/* about */
.about-photo{top:762px;left:142px;width:444px;height:444px;background:linear-gradient(135deg,#c9d3dd,#eef1f4 55%,#9aa8b6)}
.about-text{top:800px;left:630px;width:440px;font-size:13px;line-height:20px;color:var(--muted)}
.about-text h2{display:flex;align-items:center;gap:14px;font-family:'Roboto',sans-serif;font-weight:500;font-size:34px;color:var(--ink);margin-bottom:24px}
.about-text h2 .brand{font-size:32px}
.about-text p{margin-bottom:10px}
.about-text b{color:var(--blue)}
.about-text .cta{color:var(--ink);font-weight:700;font-size:14px}
.about-text .cta span{color:var(--blue);font-weight:400}

/* services */
.services{top:1290px;left:0;width:1200px;height:572px;background:var(--sky)}
.services .heading{position:absolute;top:60px;width:100%;font-size:38px}
.services .lead{position:absolute;top:128px;left:200px;width:800px;text-align:center;font-size:13px;line-height:20px;color:var(--muted)}
.svc-item{position:absolute;display:flex;align-items:center;gap:22px;font-size:19px;font-weight:600;line-height:24px}
.svc-item.left{text-align:right}
.svc-item.active .label{color:var(--blue)}
.ring{width:112px;height:112px;border-radius:50%;border:6px solid #5d5d5d;background:var(--white);display:flex;align-items:center;justify-content:center}
.svc-item.active .ring{border-color:var(--blue)}
.svc-center{position:absolute;left:498px;top:220px;width:204px;height:204px;border-radius:50%;background:var(--blue);display:flex;align-items:center;justify-content:center;color:var(--white);font-weight:800;font-size:24px;text-align:center;line-height:28px}

/* audience */
.serve .heading{position:absolute;top:1976px;left:0;width:1200px;font-size:38px}
.serve .lead{position:absolute;top:2026px;left:250px;width:700px;text-align:center;font-size:13px;line-height:20px;color:var(--muted)}
.audience{position:absolute;top:2098px;left:138px;width:924px;display:flex;justify-content:space-between}
.aud{width:152px;text-align:center;font-size:17px;line-height:21px}
.aud .disc{width:148px;height:148px;border-radius:50%;background:var(--white);box-shadow:0 0 0 6px #eeeeee,0 4px 14px rgba(0,0,0,.08);display:flex;align-items:center;justify-content:center;margin:0 auto 20px}
.aud.active .disc{box-shadow:0 0 0 6px var(--blue),0 4px 14px rgba(0,0,0,.12)}
.aud.active{color:var(--blue)}
.arrow-btn{position:absolute;width:36px;height:36px;border-radius:50%;background:var(--white);box-shadow:0 2px 8px rgba(0,0,0,.18);display:flex;align-items:center;justify-content:center}

/* team */
.team{top:2432px;left:0;width:1200px;height:662px;background:linear-gradient(180deg,#1a61b0,#1553a0)}
.team .heading{position:absolute;top:82px;width:100%;font-size:38px;color:var(--white)}
.team .sub{position:absolute;top:132px;width:100%;text-align:center;color:var(--white);font-size:20px}
.cards{position:absolute;top:192px;left:192px;width:816px;display:flex;justify-content:space-between}
.member{width:196px;height:380px;background:var(--white);padding:14px;text-align:center}
.member .photo{width:168px;height:210px;margin:0 auto 16px;background:linear-gradient(160deg,#d4d9de,#a5b0bb)}
.member h3{font-family:'Roboto',sans-serif;font-weight:500;font-size:17px;color:var(--ink);padding-top:8px;border-top:1px solid var(--line)}
.member.active h3{color:var(--blue)}
.member p{font-size:13px;color:var(--muted);margin:6px 0 10px}
.member .dots{display:flex;justify-content:center;gap:10px}
.member .dots i{width:8px;height:8px;border-radius:50%;background:#777;display:block}
.team .arrow-btn{top:414px}

/* blog */
.blog{top:3094px;left:0;width:1200px;height:644px;background:linear-gradient(180deg,#eef3f9,#f5f8fc)}
.blog .heading{position:absolute;top:72px;width:100%;font-size:38px}
.post{position:absolute;top:216px;width:450px;height:250px;background:var(--white);box-shadow:0 4px 14px rgba(0,0,0,.1);border-bottom:6px solid var(--blue);text-align:center;padding-top:100px}
.post .date{position:absolute;left:169px;top:-70px;width:112px;height:112px;border-radius:50%;background:var(--white);border:7px solid #5d5d5d;display:flex;flex-direction:column;align-items:center;justify-content:center;color:var(--blue)}
.post .date b{font-family:'Roboto',sans-serif;font-size:40px;line-height:40px;font-weight:500}
.post .date span{font-size:12px}
.post h3{font-family:'Roboto',sans-serif;font-weight:500;font-size:17px;margin-bottom:14px}
.post p{font-size:12px;line-height:17px;color:var(--muted);width:340px;margin:0 auto 12px}
.post a{font-size:13px;color:var(--blue);text-decoration:underline}
.view-all{position:absolute;top:520px;left:526px;width:148px;height:42px;border:2px solid var(--blue);color:var(--blue);background:var(--white);font-size:14px;display:flex;align-items:center;justify-content:center}
.blog .arrow-btn{top:320px}

/* contact */
.start{top:3738px;left:0;width:1200px;height:695px;background:linear-gradient(180deg,#1b62b2,#2a72c2 60%,#1b5fae)}
.start .heading{position:absolute;top:100px;width:100%;font-size:38px;color:var(--white)}
.form{position:absolute;top:183px;left:310px;width:646px;height:145px;display:grid;grid-template-columns:322px 322px;column-gap:2px}
.form .field{height:48px;border-bottom:1px solid rgba(255,255,255,.35);background:rgba(255,255,255,.06);color:rgba(255,255,255,.75);font-size:13px;padding:10px 14px}
.form .msg{grid-column:2;grid-row:1/4;height:145px;border:1px solid rgba(255,255,255,.35)}
.submit{position:absolute;top:362px;left:526px;width:148px;height:40px;background:#b9bcc0;color:var(--white);font-size:20px;font-weight:700;display:flex;align-items:center;justify-content:center}

/* footer */
.footer{top:4255px;left:0;width:1200px;height:178px}
.footer .brand{position:absolute;left:142px;top:60px;font-size:30px;color:var(--white)}
.footer .brand .mark{background:var(--white)}
.footer .links{position:absolute;left:534px;top:76px;width:530px;display:flex;justify-content:flex-end;gap:38px;font-size:12px;color:var(--white)}
.footer .copy{position:absolute;left:142px;top:142px;font-size:11px;color:#bfc3c8}
.footer .legal{position:absolute;right:136px;top:142px;font-size:11px;color:#bfc3c8}
.chat{position:absolute;left:1016px;top:-22px;width:48px;height:48px;border-radius:50%;background:var(--white);display:flex;align-items:center;justify-content:center;box-shadow:0 2px 8px rgba(0,0,0,.3)}
</style>
</head>
<body>

<!-- Top bar -->
<div class="abs topbar">
  <div class="abs contact">
    <span><svg width="14" height="14" viewBox="0 0 24 24"><path fill="#1d64b4" d="M6.6 10.8a15 15 0 0 0 6.6 6.6l2.2-2.2a1 1 0 0 1 1-.25 11.4 11.4 0 0 0 3.6.6 1 1 0 0 1 1 1V20a1 1 0 0 1-1 1A17 17 0 0 1 3 4a1 1 0 0 1 1-1h3.5a1 1 0 0 1 1 1c0 1.25.2 2.45.6 3.6a1 1 0 0 1-.25 1z"/></svg>+012-555-019</span>
    <span><svg width="16" height="12" viewBox="0 0 16 12"><rect width="16" height="12" rx="1" fill="#1d64b4"/><path d="M0 1l8 6 8-6" stroke="#fff" stroke-width="1.4" fill="none"/></svg>info@vaultmerrow.com.au</span>
  </div>
  <div class="abs follow">Follow Us on
    <i class="sq" style="background:var(--social-red);margin-left:8px"></i>
    <i class="sq" style="background:#2ea6e0"></i>
    <i class="sq" style="background:#1c5e9e"></i>
    <i class="sq" style="background:#d4332b"></i>
  </div>
</div>

<!-- Header -->
<header class="abs header">
  <div class="brand"><span class="mark"></span>Vault Merrow</div>
  <nav class="nav">
    <a class="active">HOME</a><a>ABOUT</a><a>SERVICES</a><a>RESOURCES</a><a>BLOG</a><a>CONTACT US</a>
  </nav>
</header>

<!-- Hero -->
<section class="abs hero" role="img" aria-label="Businessman holding a glowing digital security shield above an open hand on a dark blue network background">
  <h1>Because we care,<br>we’re security aware</h1>
  <div class="btn-light">Contact Us Today</div>
  <svg class="curve" width="1200" height="140" viewBox="0 0 1200 140"><path d="M0 20 Q600 200 1200 20 L1200 140 L0 140 Z" fill="#ffffff"/></svg>
</section>

<!-- About -->
<div class="abs about-photo" role="img" aria-label="Smiling businessman in a suit working on a laptop at a bright desk"></div>
<div class="abs about-text">
  <h2>About <span class="brand"><span class="mark"></span>Vault Merrow</span></h2>
  <p><b>Vault Merrow</b> It is a long established fact that a reader will be distracted by the readable content of a page when looking at its layout. The point of using Lorem Ipsum is that it has a more-or-less normal distribution.</p>
  <p>The point of using Lorem Ipsum is that it has a more-or-less normal distribution of letters, as opposed to using 'Content here, content here', making it look like readable English.</p>
  <p>Lorem Ipsum is that it has a more-or-less normal distribution of letters, as opposed to using 'Content here, content here', making it look like readable English has a more-or-less normal.</p>
  <p>The point of using Lorem Ipsum is that it has a more-or-less normal distribution of letters, as opposed to using 'Content here, content here', making it look like readable English.</p>
  <p class="cta">Get the support you need now. <span>Contact our 24/7 support line to get started.</span></p>
</div>

<!-- Services -->
<section class="abs services">
  <h2 class="heading">SERVICES</h2>
  <p class="lead"><span style="color:var(--blue)">Vault Merrow</span> It is a long established fact that a reader will be distracted by the readable content of a page when looking at its layout. The point of using Lorem Ipsum is that it has a more-or-less normal distribution of letters</p>

  <div class="svc-item left active" style="right:746px;top:220px">
    <span class="label">Data Management<br>Platforms</span>
    <span class="ring"><svg width="44" height="44" viewBox="0 0 44 44" fill="none" stroke="#1d64b4" stroke-width="2.5"><path d="M12 26a8 8 0 0 1 2-15.7A10 10 0 0 1 33 13a7 7 0 0 1-1 13H12z"/><path d="M22 26v10M16 36h12"/></svg></span>
  </div>
  <div class="svc-item left" style="right:746px;top:376px">
    <span class="label">Data Management<br>Services</span>
    <span class="ring"><svg width="40" height="44" viewBox="0 0 40 44" fill="none" stroke="#555" stroke-width="2.5"><ellipse cx="18" cy="9" rx="13" ry="5"/><path d="M5 9v24c0 3 6 5 13 5s13-2 13-5V9M5 21c0 3 6 5 13 5s13-2 13-5"/></svg></span>
  </div>
  <div class="svc-center">Vault<br>Merrow</div>
  <div class="svc-item" style="left:746px;top:220px">
    <span class="ring"><svg width="44" height="44" viewBox="0 0 44 44" fill="none" stroke="#555" stroke-width="2.5"><circle cx="17" cy="24" r="8"/><circle cx="17" cy="24" r="3"/><circle cx="31" cy="13" r="5"/></svg></span>
    <span class="label">Industry<br>Solutions</span>
  </div>
  <div class="svc-item" style="left:746px;top:376px">
    <span class="ring"><svg width="44" height="44" viewBox="0 0 44 44" fill="none" stroke="#555" stroke-width="2.5"><rect x="8" y="20" width="28" height="18" rx="2"/><path d="M14 20v-6a8 8 0 0 1 16 0v6"/></svg></span>
    <span class="label">Ransomware<br>Protection</span>
  </div>
</section>

<!-- Audience -->
<section class="serve">
  <h2 class="heading">TO WHOM WE SERVE</h2>
  <p class="lead">The point of using Lorem Ipsum is that it has a more-or-less normal distribution of letters, as opposed to using 'Content here, content here', making it look like readable English</p>
  <div class="arrow-btn" style="left:74px;top:2154px"><svg width="10" height="12"><path d="M8 1L2 6l6 5" stroke="#555" stroke-width="2" fill="none"/></svg></div>
  <div class="audience">
    <div class="aud"><div class="disc"><svg width="54" height="50" viewBox="0 0 54 50" fill="none" stroke="#555" stroke-width="2.5"><path d="M22 4L4 40h36z"/><path d="M22 18v10M22 33v2"/><circle cx="42" cy="38" r="8"/></svg></div>Risk Managers</div>
    <div class="aud"><div class="disc"><svg width="48" height="54" viewBox="0 0 48 54" fill="none" stroke="#555" stroke-width="2.5"><path d="M24 3l19 7v14c0 13-9 22-19 27C14 46 5 37 5 24V10z"/><path d="M15 27l7 7 12-13"/></svg></div>Information<br>Security</div>
    <div class="aud active"><div class="disc"><svg width="54" height="54" viewBox="0 0 54 54" fill="none" stroke="#1d64b4" stroke-width="2.5"><rect x="11" y="11" width="32" height="32" rx="3"/><rect x="20" y="25" width="14" height="11"/><path d="M23 25v-4a4 4 0 0 1 8 0v4M18 4v7M27 4v7M36 4v7M18 43v7M27 43v7M36 43v7M4 18h7M4 36h7M43 18h7M43 36h7"/></svg></div>Cyber Security<br>Professionals</div>
    <div class="aud"><div class="disc"><svg width="54" height="50" viewBox="0 0 54 50" fill="none" stroke="#555" stroke-width="2.5"><circle cx="27" cy="12" r="7"/><path d="M15 30a12 8 0 0 1 24 0"/><rect x="6" y="30" width="42" height="8"/><path d="M12 38v10M42 38v10"/></svg></div>Chief Data<br>Technicians</div>
    <div class="aud"><div class="disc"><svg width="48" height="54" viewBox="0 0 48 54" fill="none" stroke="#555" stroke-width="2.5"><circle cx="24" cy="15" r="10"/><path d="M6 50c0-12 8-18 18-18s18 6 18 18M19 36l5 8 5-8"/></svg></div>Digital Officers</div>
  </div>
  <div class="arrow-btn" style="left:1090px;top:2154px"><svg width="10" height="12"><path d="M2 1l6 5-6 5" stroke="#555" stroke-width="2" fill="none"/></svg></div>
</section>

<!-- Team -->
<section class="abs team">
  <h2 class="heading">OUR TEAM</h2>
  <p class="sub">Our Bestest Team Members.</p>
  <div class="arrow-btn" style="left:140px"><svg width="10" height="12"><path d="M8 1L2 6l6 5" stroke="#1d64b4" stroke-width="2" fill="none"/></svg></div>
  <div class="cards">
    <div class="member"><div class="photo" role="img" aria-label="Portrait of a team member in a white shirt"></div><h3>ROWAN</h3><p>Designation Here</p><div class="dots"><i></i><i></i><i></i><i></i></div></div>
    <div class="member active"><div class="photo" role="img" aria-label="Portrait of a team member in a dark blazer"></div><h3>MARA LIND</h3><p>Designation Here</p><div class="dots"><i></i><i></i><i></i><i></i></div></div>
    <div class="member"><div class="photo" role="img" aria-label="Portrait of a team member in a grey suit"></div><h3>THEO BRACK</h3><p>Designation Here</p><div class="dots"><i></i><i></i><i></i><i></i></div></div>
    <div class="member"><div class="photo" role="img" aria-label="Portrait of a team member wearing glasses and a blue shirt"></div><h3>IVO CASTEL</h3><p>Designation Here</p><div class="dots"><i></i><i></i><i></i><i></i></div></div>
  </div>
  <div class="arrow-btn" style="left:1022px"><svg width="10" height="12"><path d="M2 1l6 5-6 5" stroke="#1d64b4" stroke-width="2" fill="none"/></svg></div>
</section>

<!-- Blog -->
<section class="abs blog">
  <h2 class="heading">LATEST BLOG POSTS</h2>
  <div class="arrow-btn" style="left:84px"><svg width="10" height="12"><path d="M8 1L2 6l6 5" stroke="#555" stroke-width="2" fill="none"/></svg></div>
  <article class="post" style="left:142px">
    <div class="date"><b>12</b><span>Feb 2019</span></div>
    <h3>The point of using Lorem Ipsum</h3>
    <p>"The point of using Lorem Ipsum is that it has a more-or-less normal distribution of letters, as opposed to using 'Content here, content here', making it look like readable English others, as opposed to using content here.</p>
    <a>Learn More</a>
  </article>
  <article class="post" style="left:614px">
    <div class="date"><b>06</b><span>Feb 2019</span></div>
    <h3>The point of using Lorem Ipsum</h3>
    <p>"The point of using Lorem Ipsum is that it has a more-or-less normal distribution of letters, as opposed to using 'Content here, content here', making it look like readable English others, as opposed to using content here.</p>
    <a>Learn More</a>
  </article>
  <div class="arrow-btn" style="left:1080px"><svg width="10" height="12"><path d="M2 1l6 5-6 5" stroke="#555" stroke-width="2" fill="none"/></svg></div>
  <div class="view-all">View All</div>
</section>

<!-- Contact -->
<section class="abs start">
  <h2 class="heading">LET’S GET STARTED</h2>
  <div class="form">
    <div class="field">Your Name</div>
    <div class="field msg">Your Message</div>
    <div class="field">Your Email</div>
    <div class="field">Your Contact Number</div>
  </div>
  <div class="submit">Submit</div>
</section>

<!-- Footer -->
<footer class="abs footer">
  <svg class="abs" style="left:0;top:0" width="1200" height="178" viewBox="0 0 1200 178"><path d="M0 40 Q600 -20 1200 40 L1200 178 L0 178 Z" fill="#1e1f22"/></svg>
  <div class="chat"><svg width="26" height="24" viewBox="0 0 26 24"><path d="M3 2h20a2 2 0 0 1 2 2v12a2 2 0 0 1-2 2H10l-6 5v-5H3a2 2 0 0 1-2-2V4a2 2 0 0 1 2-2z" fill="#1d64b4"/></svg></div>
  <div class="brand"><span class="mark"></span>Vault Merrow</div>
  <nav class="links"><span>HOME</span><span>ABOUT</span><span>SERVICES</span><span>RESOURCES</span><span>BLOG</span><span>CONTACT US</span></nav>
  <p class="copy">Copyright 2019 @ Vault Merrow. All Rights Reserved.</p>
  <p class="legal">Terms of services | Privacy Policy</p>
</footer>

</body>
</html>
```